Quillbay.vc needs a better website design!

We need a new and better website for Quillbay.vc. We're a Canadian venture capital firm that invests in innovative entrepreneurs. We compete against the following websites: tormelo.vc, brightvalefund.ca, kestrowvc.com, and dovaran.vc. We're a diverse group of partners and we're dedicated to the founders we invest in.
Updates

I don’t really like stock photos of random people as part of the website design…so please try to stay away from using those images. Thanks, Owen

Target Market(s)

Canadian entrepreneurs and investors

Industry/Entity Type

Venture capital, finance, investment, entrepreneurship

Coding

Coded - Design and coding required

Number of Pages Required

4 page

Font styles to use
Sans Serif

Colors

Designer to choose colors to be used in the design.

Requirements
Must have
• Clean crisp overall design. Fast and to the point.
Nice to have
• Check out www.quillbay.vc - I did it myself and it is too basic and too wordy.
Should not have
• No stock images with random people in them! Not too wordy or with too many large images that are slow to load.

```html
<!DOCTYPE html>
<html lang="en">
<head>
<meta charset="utf-8">
<title>Quillbay.vc</title>
<link href="https://fonts.googleapis.com/css2?family=Poppins:wght@300;400;500;600&display=swap" rel="stylesheet">
<style>
:root{
  --green:#7a962f;
  --green-dark:#6a8526;
  --green-pale:#edf2d8;
  --ink:#1f2a10;
  --text:#3a3a3a;
  --muted:#6b6b6b;
  --line:#e3e3e3;
  --footer:#f7f7f7;
  --white:#ffffff;
}
*{margin:0;padding:0;box-sizing:border-box}
html,body{width:667px;height:1200px;overflow:hidden}
body{position:relative;font-family:'Poppins',sans-serif;color:var(--text);background:var(--white)}
.abs{position:absolute}

/* header */
.site-header{left:0;top:0;width:667px;height:54px;background:var(--white)}
.brand{left:90px;top:14px;display:flex;align-items:center;gap:5px;font-weight:600;font-size:11px;color:var(--green)}
.brand-dot{width:10px;height:10px;border-radius:50%;background:var(--green)}
.nav-item{top:0;height:56px;line-height:54px;font-size:8px;color:var(--muted);text-align:center}
.nav-item.active{background:#f4f4f4;color:var(--green);border-bottom:2px solid var(--green)}

/* hero */
.hero{left:0;top:54px;width:667px;height:330px;overflow:hidden}
.hero-photo{position:absolute;inset:0;background:linear-gradient(180deg,#5c5a55 0%,#6b7a72 30%,#3f6f78 55%,#2f4a33 80%,#2c3d27 100%)}
.hero-plant{position:absolute;left:510px;top:140px;width:130px;height:220px;border-radius:60% 40% 10% 10%;background:var(--green);opacity:.85}
.hero-title{left:70px;top:114px;width:507px;text-align:center;color:var(--white);font-weight:300;font-size:17px;line-height:28px}
.numbers-title{left:185px;top:235px;width:298px;text-align:center;color:var(--white);font-size:12px;display:flex;align-items:center;gap:7px}
.numbers-title::before,.numbers-title::after{content:"";flex:1;height:1px;background:rgba(255,255,255,.35)}
.stat{top:262px;width:91px;height:34px;border:1px solid rgba(255,255,255,.35);border-left:3px solid var(--green);color:var(--white);display:flex;align-items:center;gap:5px;padding-left:9px}
.stat b{font-weight:500;font-size:20px;line-height:1}
.stat span{font-size:8px;line-height:10px}
.wave{left:0;top:320px;width:667px;height:70px}

/* intro */
.intro{left:150px;top:403px;width:367px;text-align:center;font-weight:300;font-size:15px;line-height:24px;color:var(--text)}
.card{top:470px;width:233px;height:150px;background:var(--green-pale);border:1px solid #dfe8c2;border-radius:2px;overflow:hidden}
.card svg.icon{position:absolute;left:19px;top:28px}
.card p{position:absolute;left:19px;top:77px;width:160px;font-weight:300;font-size:9.5px;line-height:15px;color:var(--text)}
.card-leaf{position:absolute;right:-12px;top:45px;width:60px;height:110px;border-radius:50% 50% 50% 50%/60% 60% 40% 40%;background:#e4e4e4}

/* portfolio */
.portfolio-title{left:0;top:668px;width:667px;text-align:center;font-weight:600;font-size:15px;color:var(--ink)}
.tile{width:85px;height:38px;background:var(--white);border:1px solid #ececec;box-shadow:0 1px 3px rgba(0,0,0,.06);display:flex;align-items:center;justify-content:center;gap:3px;font-weight:500;font-size:9px;color:#2d2d2d}
.tile i{width:6px;height:6px;border-radius:50%;background:var(--green);display:block}

/* call to action */
.cta{left:0;top:849px;width:667px;height:222px;background:linear-gradient(135deg,var(--green-dark),var(--green) 50%,#7f9b33)}
.cta-mark{position:absolute;left:90px;top:27px;width:194px;height:194px;border-radius:50%;background:rgba(255,255,255,.14)}
.cta-title{left:304px;top:74px;font-weight:500;font-size:29px;line-height:36px;color:var(--white)}
.cta-sub{left:304px;top:147px;font-weight:500;font-size:16px;color:var(--white)}

/* footer */
.site-footer{left:0;top:1071px;width:667px;height:104px;background:var(--footer)}
.foot-link{top:16px;font-size:8px;color:#333;text-align:center;width:70px}
.foot-sep{top:18px;width:1px;height:9px;background:#ddd}
.foot-rule{left:90px;top:49px;width:487px;height:1px;background:var(--line)}
.touch{right:344px;top:61px;text-align:right;color:var(--ink)}
.touch h3,.follow h3{font-weight:400;font-size:11px}
.touch p{font-size:8px;margin-top:3px}
.touch p b{font-weight:500}
.foot-vline{left:333px;top:61px;width:1px;height:34px;background:var(--line)}
.follow{left:341px;top:60px;color:var(--ink)}
.socials{display:flex;gap:3px;margin-top:4px}
.socials span{width:11px;height:11px;border-radius:50%;background:#1da1f2}
.socials span+span{background:#0a66c2}
.copyright{left:0;top:1175px;width:667px;height:25px;background:var(--green);color:var(--white);font-size:8px;text-align:center;line-height:25px;font-weight:500}
</style>
</head>
<body>

<header class="abs site-header">
  <div class="abs brand"><span class="brand-dot"></span>QUILLBAY.VC</div>
  <a class="abs nav-item active" style="left:391px;width:36px">Home</a>
  <a class="abs nav-item" style="left:440px;width:40px">What</a>
  <a class="abs nav-item" style="left:487px;width:40px">Who</a>
  <a class="abs nav-item" style="left:534px;width:50px">Portfolio</a>
</header>

<section class="abs hero">
  <div class="hero-photo" role="img" aria-label="Mountain lake landscape with forested shores"></div>
  <div class="hero-plant" role="img" aria-label="Large green sprouting plant illustration"></div>
</section>
<h1 class="abs hero-title">Quillbay.vc is a venture capital firm that invests in innovative seed-stage technology companies in western canada focused on b2b and saas markets.</h1>
<div class="abs numbers-title">Quillbay.vc In Numbers</div>
<div class="abs stat" style="left:185px"><b>10</b><span>Portfolio<br>companies</span></div>
<div class="abs stat" style="left:287px"><b>7</b><span>Follow-on<br>financings</span></div>
<div class="abs stat" style="left:390px"><b>100</b><span>+<br>Employees</span></div>
<svg class="abs wave" viewBox="0 0 667 70" preserveAspectRatio="none">
  <path d="M0 43 C80 10 170 5 280 20 C380 35 430 62 520 60 C590 58 630 45 667 33 L667 70 L0 70 Z" fill="#7a962f"/>
  <path d="M0 52 C80 22 170 16 280 30 C380 45 430 72 520 70 C590 68 630 54 667 42 L667 70 L0 70 Z" fill="#ffffff"/>
</svg>

<p class="abs intro">We are serial entrepreneurs and venture capital investors who provide</p>

<div class="abs card" style="left:90px">
  <svg class="icon" width="46" height="44" viewBox="0 0 46 44" fill="none" stroke="#555" stroke-width="1.8">
    <rect x="1" y="32" width="7" height="10" rx="1"/><rect x="12" y="25" width="7" height="17" rx="1"/>
    <rect x="23" y="17" width="7" height="25" rx="1"/><rect x="34" y="8" width="7" height="34" rx="1"/>
    <path d="M3 18 C14 16 22 11 30 3" stroke="#7a962f"/><path d="M25 3 L31 2 L31 8" stroke="#7a962f"/>
  </svg>
  <p>Mentoring and strategic advice to help you grow your company quickly and efficiently</p>
  <div class="card-leaf" role="img" aria-label="Soft grey leaf shape"></div>
</div>
<div class="abs card" style="left:344px">
  <svg class="icon" width="42" height="44" viewBox="0 0 42 44" fill="none" stroke="#555" stroke-width="1.8">
    <rect x="1" y="14" width="22" height="16" rx="3"/><path d="M6 14 V10 H18 V14"/>
    <circle cx="28" cy="31" r="11" stroke="#7a962f"/>
    <path d="M32 26 C30 24 24 24 24 28 C24 32 32 30 32 34 C32 38 26 38 24 36 M28 22 V40" stroke="#7a962f"/>
  </svg>
  <p>Investor introductions to help you raise additional follow-on funding for your startup</p>
  <div class="card-leaf" role="img" aria-label="Soft grey leaf shape"></div>
</div>

<h2 class="abs portfolio-title">Check out our innovative portfolio companies!</h2>
<div class="abs tile" style="left:90px;top:709px"><i></i>Tidemark Labs</div>
<div class="abs tile" style="left:190px;top:709px"><i></i>Corvane</div>
<div class="abs tile" style="left:290px;top:709px"><i></i>Lumenreach</div>
<div class="abs tile" style="left:391px;top:709px"><i></i>Brisklane</div>
<div class="abs tile" style="left:491px;top:709px"><i></i>Ostria</div>
<div class="abs tile" style="left:90px;top:758px"><i></i>Pellaro</div>
<div class="abs tile" style="left:190px;top:758px"><i></i>Vantrix</div>
<div class="abs tile" style="left:290px;top:758px"><i></i>Keystile</div>
<div class="abs tile" style="left:391px;top:758px"><i></i>Clarion Home</div>
<div class="abs tile" style="left:491px;top:758px"><i></i>Nutrevo</div>

<section class="abs cta">
  <div class="cta-mark" role="img" aria-label="Large faint brand emblem"></div>
  <h2 class="abs cta-title">If you have what<br>we're looking for</h2>
  <p class="abs cta-sub">Contact us today</p>
</section>

<footer class="abs site-footer">
  <span class="abs foot-sep" style="left:178px"></span>
  <a class="abs foot-link" style="left:178px">Home</a>
  <span class="abs foot-sep" style="left:253px"></span>
  <a class="abs foot-link" style="left:257px">What</a>
  <span class="abs foot-sep" style="left:332px"></span>
  <a class="abs foot-link" style="left:337px">Who</a>
  <span class="abs foot-sep" style="left:409px"></span>
  <a class="abs foot-link" style="left:416px">Portfolio</a>
  <span class="abs foot-sep" style="left:487px"></span>
  <div class="abs foot-rule"></div>
  <div class="abs touch"><h3>Get In Touch</h3><p><b>Email:</b> info@quillbay.vc</p></div>
  <div class="abs foot-vline"></div>
  <div class="abs follow"><h3>Follow Us</h3><div class="socials"><span></span><span></span></div></div>
</footer>
<div class="abs copyright">Copyright © 2021 Quillbay.vc - All Rights Reserved.</div>

</body>
</html>
```